Harrowgate Care Assurance Ltd needs a business card and logo

We need a logo for documents, invoices etc and a business card to match. We are a health auditing, training and consulting company based in NZ and working in both Australia and NZ. We ensure health organisations meet all their compliance requirements and develop expertise in the health auditing sector. The design should in some way reflect either symbols for quality management in the health sector.

Target Market(s)

Health providers and those wishing to increase their capability in meeting and understanding compliance requirements

Industry/Entity Type

Business

Contact Information for Business Card

Logo plus contact details

Logo Text

Health auditing, consultancy and training

Requirements
Must have
• Name and contact details director: Marla Fenwick, mfenwick@hca-example.co.nz, PO Box 318, Warkworth, NZ, cell +6427391652

```html
<!DOCTYPE html>
<html lang="en">
<head>
<meta charset="utf-8">
<title>Harrowgate Care Assurance Ltd – Business Card</title>
<link rel="stylesheet" href="https://fonts.googleapis.com/css2?family=Source+Sans+3:wght@400;600;700&display=swap">
<style>
  :root {
    --stage: #000000;
    --leaf-light: #6cb432;
    --leaf-mid: #4a9e22;
    --leaf-deep: #1f7f10;
    --leaf-shade: #2e8a18;
    --ink-light: #ffffff;
    --ink-soft: #ecefe6;
  }
  html, body {
    margin: 0;
    padding: 0;
    width: 1200px;
    height: 900px;
    overflow: hidden;
    background: var(--stage);
  }
  .canvas {
    position: relative;
    width: 1200px;
    height: 900px;
    background: var(--stage);
    font-family: "Source Sans 3", "Myriad Pro", sans-serif;
  }
  .card {
    position: absolute;
    top: 275px;
    width: 477px;
    height: 293px;
    overflow: hidden;
    background:
      radial-gradient(ellipse 40% 35% at 25% 20%, rgba(120,190,60,0.55), transparent 70%),
      radial-gradient(ellipse 35% 30% at 75% 30%, rgba(40,130,20,0.5), transparent 70%),
      radial-gradient(ellipse 45% 40% at 60% 80%, rgba(25,125,12,0.6), transparent 70%),
      radial-gradient(ellipse 40% 35% at 15% 75%, rgba(90,170,45,0.45), transparent 70%),
      linear-gradient(165deg, var(--leaf-light) 0%, var(--leaf-mid) 45%, var(--leaf-shade) 75%, var(--leaf-deep) 100%);
  }
  .card--contact {
    left: 116px;
    border-radius: 0 62px 0 62px;
  }
  .card--brand {
    left: 622px;
    border-radius: 62px 0 62px 0;
  }
  .contact {
    position: absolute;
    left: 0;
    right: 0;
    top: 72px;
    text-align: center;
    color: var(--ink-light);
  }
  .contact p { margin: 0; }
  .contact__name {
    font-weight: 700;
    font-size: 18px;
    line-height: 22px;
  }
  .contact__role {
    font-size: 13px;
    line-height: 17px;
  }
  .contact__phone {
    margin-top: 29px !important;
    font-size: 13px;
    line-height: 20px;
  }
  .contact__email {
    font-size: 13px;
    line-height: 20px;
  }
  .contact__address {
    margin-top: 18px !important;
    font-size: 13px;
    line-height: 20px;
  }
  .brand {
    position: absolute;
    left: 0;
    right: 0;
    top: 98px;
    text-align: center;
    color: var(--ink-soft);
    font-weight: 600;
    font-size: 34px;
    line-height: 40px;
    letter-spacing: 1px;
    text-transform: uppercase;
  }
</style>
</head>
<body>
  <main class="canvas">
    <section class="card card--contact" aria-label="Business card, contact side">
      <div class="contact">
        <p class="contact__name">Marla Fenwick</p>
        <p class="contact__role">Director</p>
        <p class="contact__phone">+6427391652</p>
        <p class="contact__email">mfenwick@hca-example.co.nz</p>
        <p class="contact__address">PO Box 318, Warkworth, NZ</p>
      </div>
    </section>
    <section class="card card--brand" aria-label="Business card, brand side">
      <p class="brand">Harrowgate Care<br>Assurance Ltd</p>
    </section>
  </main>
</body>
</html>
```